Cellar Crew Poster / Flyer Ad Design

We need a poster design (and a complimentary A6 flyer) to promote our Adult Rock Band Course called 'Cellar Crew'.

Target market is adults aged 25 - 50 primarily

Design to be eye catching, creative, appealing and easy to understand. Most of the distribution will be street marketing, email marketing, social media, music magazines and websites and to other music teachers.

We need the design to be as an A3 and A4 poster and an A6 promo flyer/e-flyer. Should look good in colour and we'll want a version in black and white.

Would be good to also incorporate our music school logo (just for branding purposes).

Text as follows:

CELLAR CREW
The Ultimate Rock Band Course for Adults

Ever wondered what it would be like to play in a band?

Feeling musically rusty and looking for a way to start playing your instrument again?

Then here’s an exciting opportunity you can’t miss!

All musical levels
Beginner/Intermediate to Advanced Players

Limited Numbers

REGISTER ONLINE NOW
www.tunevaleacademy.com.au

Starts Saturday 3rd August
Newtown

Over 6 exciting weekends you’ll work with one of our experienced professional band coaches and transform yourselves into the ultimate ‘Cellar Crew’

Discover how to play in a band
Revisit your musical abilities
Practice songs
Perform on Stage

Drummers, Bass Guitarists, Singers, Keys, Guitarists, Saxophone, Percussionists and others all welcome to join

For more information, course costs and registration, please visit www.tunevaleacademy.com.au or call 02 7194 2851 / 0438 672 904

Reason: Hi Everyone, I've been away and unable to respond to some of the designs because I've been ill. Have decided to extend the deadline and now commit to paying designers. Look forward to seeing more designs. Any questions, please let me know. Thanks Mirela

```html
<!DOCTYPE html>
<html lang="en">
<head>
<meta charset="utf-8">
<title>Cellar Crew – The Ultimate Rock Band Course for Adults</title>
<link rel="stylesheet" href="https://fonts.googleapis.com/css2?family=Delius&family=Rubik+Dirt&family=Cabin:ital,wght@0,400;1,400&display=swap">
<style>
  :root {
    --top-field: #7b7062;
    --top-field-light: #8a7f6f;
    --band-teal: #6fa39a;
    --bottom-field: #9b8174;
    --bottom-field-light: #a68c7e;
    --ink: #161412;
    --ink-soft: #2b2a28;
    --logo-panel: #f4f2ef;
    --logo-ink: #6b7f86;
    --logo-dot: #8a6a5c;
  }
  * { margin: 0; padding: 0; box-sizing: border-box; }
  html, body { width: 848px; height: 1200px; overflow: hidden; background: #ffffff; }
  .poster { position: relative; width: 848px; height: 1200px; overflow: hidden; font-family: "Delius", "Comic Sans MS", cursive; color: var(--ink); }

  .pattern-field { position: absolute; left: 0; width: 848px; }
  .pattern-field--top { top: 0; height: 472px; background: radial-gradient(ellipse at 50% 40%, var(--top-field-light), var(--top-field)); }
  .pattern-field--bottom { top: 732px; height: 468px; background: radial-gradient(ellipse at 50% 50%, var(--bottom-field-light), var(--bottom-field)); }

  .line { position: absolute; left: 0; width: 848px; white-space: nowrap; }
  .line--left { left: 55px; width: auto; text-align: left; }
  .line--center { text-align: center; }

  .intro { font-size: 25px; line-height: 33px; }
  .levels { font-size: 23px; }
  .register { font-size: 24px; line-height: 37px; }

  .title-band { position: absolute; top: 472px; left: 0; width: 848px; height: 260px; background: var(--band-teal); }
  .course-title { position: absolute; top: 24px; left: 0; width: 848px; text-align: center; font-family: "Rubik Dirt", "Impact", sans-serif; font-size: 92px; letter-spacing: 2px; color: var(--ink); line-height: 1; }
  .course-tagline { position: absolute; top: 118px; left: 74px; font-family: "Cabin", "Helvetica", sans-serif; font-style: italic; font-size: 29px; color: var(--ink-soft); }
  .course-contact { position: absolute; top: 188px; left: 0; width: 848px; text-align: center; font-family: "Cabin", "Helvetica", sans-serif; font-size: 17px; line-height: 22px; color: var(--ink-soft); }
  .course-contact .italic { font-style: italic; }

  .details { font-size: 27px; line-height: 36px; }
  .benefits { font-size: 27px; line-height: 36.5px; }

  .brand-mark { position: absolute; left: 555px; top: 1138px; width: 293px; height: 62px; background: var(--logo-panel); display: flex; align-items: center; padding-left: 14px; gap: 12px; }
  .brand-mark__name { font-family: "Delius", "Comic Sans MS", cursive; font-size: 24px; color: var(--logo-ink); }
  .brand-mark__dot { width: 36px; height: 36px; border-radius: 50%; background: var(--logo-dot); }
</style>
</head>
<body>
<main class="poster">
  <div class="pattern-field pattern-field--top" role="img" aria-label="Repeating pattern of pale instrument silhouettes on a brown-grey field"></div>

  <section class="intro-copy">
    <p class="line line--left intro" style="top:26px">Ever wondered what it would be like to play in a band?</p>
    <p class="line line--left intro" style="top:100px">Feeling musically rusty and looking for a way to start<br>playing your instrument again?</p>
    <p class="line line--left intro" style="top:205px">Then here’s an exciting opportunity you can’t miss!</p>
    <p class="line line--center levels" style="top:288px">All musical levels : Beginner/Intermediate to Advanced Players</p>
    <p class="line line--center register" style="top:348px">Limited Numbers REGISTER ONLINE NOW<br>www.tunevaleacademy.com.au<br>Starts Saturday 3rd August Newtown</p>
  </section>

  <header class="title-band">
    <h1 class="course-title">CELLAR CREW</h1>
    <p class="course-tagline">The Ultimate Rock Band Course for Adults</p>
    <p class="course-contact">For more information, course costs and registration,<br><span class="italic">please visit www.tunevaleacademy.com.au or call 02 7194 2851 / 0438 672 904</span></p>
  </header>

  <div class="pattern-field pattern-field--bottom" role="img" aria-label="Repeating pattern of green instrument silhouettes on a mauve-brown field"></div>

  <section class="course-details">
    <p class="line line--center details" style="top:756px">Over 6 exciting weekends you’ll work with one of our<br>experienced professional band coaches and transform<br>yourselves into the ultimate ‘Cellar Crew’</p>
    <p class="line line--center benefits" style="top:900px">Discover how to play in a band<br>Revisit your musical abilities<br>Practice songs<br>Perform on Stage<br>Drummers, Bass Guitarists, Singers, Keys, Guitarists,<br>Saxophone, Percussionists and others all welcome to join</p>
  </section>

  <div class="brand-mark">
    <span class="brand-mark__name">Tunevale Academy</span>
    <span class="brand-mark__dot"></span>
  </div>
</main>
</body>
</html>
```